New Business Card Design Project

I need a design for business cards, i am an electrical business called "Corvane Electrical and Communications" i need the cards to be double sided with the company logo on the back (attached) the front needs to say my company name, web site, email address, telephone number, and ABN number and electrical license number. I am open to different arrangements of the information but would like the background to be incorporating something electrical or something that looks smart. open to all additional ideas also.

The company colours are orange and grey see logo attached.

Business Name: Corvane Electrical and Communications
Website: corvaneelectricalandcomms.example.com.au
Email: brent@corvaneelectricalandcomms.example.com.au
Telephone(mobile): 0481209736
ABN: 71208349162
Lic No: 418273D

Target Market(s)

Business entities, Project Managers, Accounts, Clients

Industry/Entity Type

Electrician

Contact Information for Business Card

I need a design for business cards, i am an electrical business called "Corvane Electrical and Communications" i need the cards to be double sided with the company logo on the back (attached) the front needs to say my company name

Font styles to use
Serif
Sans Serif

Colors
f37122
5c5c5c

Requirements
Must have
• Must have the Logo on the back open to different ways of it being on the back but had in mind to keep it central but again open to other options
Nice to have
• A real modern cool background that is eye catching yet contemporary
Should not have
• No backgrounds of a light bulb or plug or anything like that

```html
<!DOCTYPE html>
<html lang="en">
<head>
<meta charset="utf-8">
<title>Corvane Electrical and Communications – Business Card</title>
<link href="https://fonts.googleapis.com/css2?family=Open+Sans:wght@400;600;700&display=swap" rel="stylesheet">
<style>
  :root {
    --backdrop: #3f3834;
    --card: #0d0d0d;
    --card-edge: #1a1a1a;
    --orange: #f5a31a;
    --white: #f2f2f2;
    --silver: #c9c9c9;
    --rule: #6b5a2a;
  }
  * { margin: 0; padding: 0; box-sizing: border-box; }
  html, body {
    width: 1200px; height: 900px; overflow: hidden;
    background: var(--backdrop);
    font-family: "Open Sans", Arial, sans-serif;
  }
  .stage {
    position: relative; width: 1200px; height: 900px;
    display: flex; align-items: center; justify-content: center; gap: 30px;
  }
  .card {
    width: 560px; height: 330px;
    background: var(--card);
    border: 1px solid var(--card-edge);
    box-shadow: 0 10px 30px rgba(0,0,0,.45);
    position: relative;
    overflow: hidden;
  }
  /* front */
  .card-front { display: flex; align-items: center; padding-right: 24px; }
  .brand {
    width: 200px; flex: none; padding-left: 28px; padding-top: 90px;
    color: var(--white); font-weight: 600;
  }
  .brand-mark { display: flex; align-items: center; gap: 7px; }
  .brand-dot { width: 11px; height: 11px; border-radius: 50%; background: var(--orange); flex: none; }
  .brand-name { font-size: 28px; line-height: 1; letter-spacing: 1px; }
  .brand-tagline {
    font-size: 8.5px; letter-spacing: .4px; margin-top: 6px;
    text-transform: uppercase; white-space: nowrap;
  }
  .divider { width: 1px; height: 170px; background: var(--rule); margin-top: 20px; flex: none; }
  .details {
    padding-left: 14px; padding-top: 10px; min-width: 0;
    color: var(--white); font-size: 12.5px; line-height: 1.45;
  }
  .person-name { color: var(--orange); font-weight: 700; font-size: 15px; }
  .person-role { margin-bottom: 12px; }
  .ids { margin-bottom: 12px; }
  .contact-row { display: flex; align-items: center; gap: 7px; white-space: nowrap; font-size: 11.5px; }
  .contact-row svg { width: 11px; height: 11px; flex: none; fill: var(--orange); }
  /* back */
  .card-back { display: flex; align-items: center; justify-content: center; }
  .back-brand { color: var(--silver); font-weight: 600; }
  .back-brand .brand-name { font-size: 44px; }
  .back-brand .brand-tagline { font-size: 13px; letter-spacing: .6px; }
  .back-brand .brand-dot { width: 16px; height: 16px; background: var(--silver); }
</style>
</head>
<body>
<main class="stage">
  <section class="card card-front" aria-label="Card front">
    <div class="brand">
      <div class="brand-mark"><span class="brand-dot"></span><span class="brand-name">Corvane</span></div>
      <div class="brand-tagline">Electrical &amp; Communications</div>
    </div>
    <div class="divider"></div>
    <div class="details">
      <div class="person-name">Brent Halloway</div>
      <div class="person-role">Director</div>
      <div class="ids">
        <div>ABN: 71208349162</div>
        <div>Lic No: 418273D</div>
      </div>
      <div class="contact-row">
        <svg viewBox="0 0 24 24"><path d="M6.6 10.8a15 15 0 006.6 6.6l2.2-2.2c.3-.3.7-.4 1-.2 1.1.4 2.3.6 3.6.6.6 0 1 .4 1 1V20c0 .6-.4 1-1 1A17 17 0 013 4c0-.6.4-1 1-1h3.5c.6 0 1 .4 1 1 0 1.3.2 2.5.6 3.6.1.3 0 .7-.2 1z"/></svg>
        <span>0481209736</span>
      </div>
      <div class="contact-row">
        <svg viewBox="0 0 24 24"><path d="M2 5h20v14H2z M2 5l10 8 10-8" stroke="#0d0d0d" stroke-width="1.5"/></svg>
        <span>brent@corvaneelectricalandcomms.example.com.au</span>
      </div>
      <div class="contact-row">
        <svg viewBox="0 0 24 24"><circle cx="12" cy="12" r="10"/><path d="M2 12h20M12 2c3 3 3 17 0 20M12 2c-3 3-3 17 0 20" stroke="#0d0d0d" stroke-width="1.5" fill="none"/></svg>
        <span>corvaneelectricalandcomms.example.com.au</span>
      </div>
    </div>
  </section>

  <section class="card card-back" aria-label="Card back">
    <div class="back-brand">
      <div class="brand-mark"><span class="brand-dot"></span><span class="brand-name">Corvane</span></div>
      <div class="brand-tagline">Electrical &amp; Communications</div>
    </div>
  </section>
</main>
</body>
</html>
```